Puffy Clouds Cotton Candy

Looking for a logo design and business cards to help a 13 year old entrepreneur promote her cotton candy business.
Contact Information for Business Card
Name, Phone & Email
Colors
E54698
E96AAD
F1A4CE
F9D9EA
FCEFF6
A7469A
B969AE
D3A5CF
EDDBEB
F8F0F9
6B429C
8869AF
B7A5CE
E3DAEB
F3F0F8
Requirements
Must have
- A fun feel that is appropriate for a teenage girl selling cotton candy

```html
<!DOCTYPE html>
<html lang="en">
<head>
<meta charset="utf-8">
<title>Puffy Clouds Cotton Candy – Business Card</title>
<link href="https://fonts.googleapis.com/css2?family=Montserrat:wght@500;700&display=swap" rel="stylesheet">
<style>
  :root {
    --pink: #E54698;
    --pink-soft: #E96AAD;
    --purple: #6B429C;
    --white: #FFFFFF;
    --ink: #1d1d1d;
    --backdrop: #2a2a2a;
  }
  * { box-sizing: border-box; margin: 0; padding: 0; }
  html, body { width: 1200px; height: 1015px; overflow: hidden; }
  body {
    background: var(--backdrop);
    font-family: "Montserrat", sans-serif;
    position: relative;
  }
  .card {
    position: absolute;
    left: 240px;
    width: 720px;
    height: 410px;
    overflow: hidden;
  }
  /* Back side */
  .card-back { top: 55px; background: var(--pink); }
  .card-back .brand {
    position: absolute;
    left: 56px;
    bottom: 56px;
    color: var(--white);
    font-weight: 700;
    line-height: 1.05;
  }
  .card-back .brand-main { font-size: 50px; display: block; }
  .card-back .brand-sub { font-size: 34px; display: block; }

  /* Front side */
  .card-front { top: 550px; background: var(--white); }
  .front-header {
    position: absolute;
    top: 0; left: 0; right: 0;
    height: 150px;
    display: flex;
    align-items: center;
    justify-content: center;
    gap: 26px;
  }
  .brand-dot {
    width: 96px; height: 96px;
    border-radius: 50%;
    border: 5px solid var(--pink);
    flex: none;
  }
  .front-header .brand {
    color: var(--pink);
    font-weight: 700;
    line-height: 1.05;
  }
  .front-header .brand-main { font-size: 40px; display: block; }
  .front-header .brand-sub { font-size: 28px; display: block; }

  .info-band {
    position: absolute;
    top: 150px; left: 0; right: 0;
    height: 150px;
    background: var(--pink);
    color: var(--white);
    display: flex;
    align-items: center;
    justify-content: center;
    gap: 30px;
  }
  .person { text-align: right; }
  .person-name { font-size: 30px; font-weight: 700; }
  .person-role { font-size: 19px; font-weight: 500; }
  .divider { width: 2px; height: 84px; background: var(--white); }
  .contact-list { list-style: none; font-size: 19px; font-weight: 500; }
  .contact-list li { display: flex; align-items: center; gap: 12px; line-height: 1.6; }
  .contact-list svg { width: 20px; height: 20px; flex: none; }

  .address {
    position: absolute;
    top: 300px; left: 0; right: 0;
    height: 86px;
    display: flex;
    align-items: center;
    justify-content: center;
    font-size: 22px;
    font-weight: 500;
    color: var(--ink);
  }
  .foot-bar { position: absolute; bottom: 0; left: 0; right: 0; height: 24px; display: flex; }
  .foot-pink { flex: 55; background: var(--pink); }
  .foot-purple { flex: 45; background: var(--purple); }
</style>
</head>
<body>
  <section class="card card-back" aria-label="Business card back">
    <p class="brand">
      <span class="brand-main">Puffy Clouds</span>
      <span class="brand-sub">Cotton Candy</span>
    </p>
  </section>

  <section class="card card-front" aria-label="Business card front">
    <header class="front-header">
      <span class="brand-dot" aria-hidden="true"></span>
      <p class="brand">
        <span class="brand-main">Puffy Clouds</span>
        <span class="brand-sub">Cotton Candy</span>
      </p>
    </header>

    <div class="info-band">
      <div class="person">
        <p class="person-name">Maya Ellison</p>
        <p class="person-role">Managing Director</p>
      </div>
      <span class="divider" aria-hidden="true"></span>
      <ul class="contact-list">
        <li>
          <svg viewBox="0 0 24 24" aria-hidden="true"><path fill="#fff" d="M6.6 10.8a15.1 15.1 0 0 0 6.6 6.6l2.2-2.2a1 1 0 0 1 1-.25 11.4 11.4 0 0 0 3.6.57 1 1 0 0 1 1 1V20a1 1 0 0 1-1 1A17 17 0 0 1 3 4a1 1 0 0 1 1-1h3.5a1 1 0 0 1 1 1c0 1.25.2 2.45.57 3.57a1 1 0 0 1-.25 1z"/></svg>
          044-987 654 321
        </li>
        <li>
          <svg viewBox="0 0 24 24" aria-hidden="true"><rect x="2" y="5" width="20" height="14" fill="none" stroke="#fff" stroke-width="2"/><path d="M2 5l10 8 10-8" fill="none" stroke="#fff" stroke-width="2"/></svg>
          hello@puffyclouds.com
        </li>
      </ul>
    </div>

    <p class="address">87, Maple Lane, Sugar Hill 30518, Country Name</p>

    <div class="foot-bar" aria-hidden="true">
      <span class="foot-pink"></span>
      <span class="foot-purple"></span>
    </div>
  </section>
</body>
</html>
```